Vellow Crest personal care products line

I need a label design for a line of shampoo, conditioner, beard oil, body butter, massage oil, all containing Hemp oil, All Natural product. No phosphates,
I want the design to feel unisex but want to keep it clean as possible. This is for upscale salons and needs to say on the label professional styling products on the label. Please visit my facebook page www.pagebook-sample.com/vellowcrest to see the description of the product benefits. I am attaching some ideas I like as well as the vellow crest logo. I would like to see any color of bottle you best think will suit this product as well as new logo design. I am not set on any of these elements. Just the name Vellow Crest.
Updates

Project Deadline Extended Reason: I have extended the deadline as I had not filled out the description for the design as it should be. I have also added some features that will define the idea as to what we need. I am open to any desing using Vellow Crest. The tag line is not anything I am determined to keep either. Please just be creative and help come up with a great product label for this name and product.Thank you to all ! Added Tuesday, June 2, 2015

Target Market(s)

Salons and upper end market

Industry/Entity Type

Cosmetology

Font styles to use
Serif
Sans Serif

Requirements
Must have
• Logo
Nice to have
• Bottle and packaging ideas on color and shape of bottle

```html
<!DOCTYPE html>
<html lang="en">
<head>
<meta charset="utf-8">
<title>Vellow Crest Shampoo Label</title>
<link rel="stylesheet" href="https://fonts.googleapis.com/css2?family=Lato:wght@300;400;900&family=Kreon:wght@300&family=Crimson+Text:ital@1&display=swap">
<style>
  :root {
    --plum: #8a1a55;
    --plum-dark: #6a1040;
    --plum-light: #9e1f62;
    --leaf: #3cb44c;
    --paper: #f3f3f3;
    --ink: #5a5a5a;
  }
  html, body {
    margin: 0;
    padding: 0;
    overflow: hidden;
    background: var(--paper);
  }
  .label {
    position: relative;
    width: 1034px;
    height: 1200px;
    background: var(--paper);
    overflow: hidden;
  }
  .band {
    position: absolute;
    left: 0;
    width: 1034px;
    height: 110px;
  }
  .band--top { top: 0; }
  .band--bottom { bottom: 0; }
  .brand-mark {
    position: absolute;
    left: 377px;
    top: 140px;
    width: 280px;
    height: 280px;
    border-radius: 50%;
    background: var(--leaf);
  }
  .brand-name {
    position: absolute;
    top: 510px;
    left: 0;
    width: 1034px;
    text-align: center;
    font-family: "Lato", sans-serif;
    font-weight: 900;
    font-size: 60px;
    letter-spacing: 2px;
    color: var(--plum);
    text-transform: uppercase;
    line-height: 1;
  }
  .tagline {
    position: absolute;
    top: 586px;
    left: 0;
    width: 1034px;
    text-align: center;
    font-family: "Lato", sans-serif;
    font-weight: 400;
    font-size: 25px;
    color: var(--ink);
    line-height: 1.2;
  }
  .product-name {
    position: absolute;
    top: 716px;
    left: 0;
    width: 1034px;
    text-align: center;
    font-family: "Kreon", serif;
    font-weight: 300;
    font-size: 54px;
    color: var(--leaf);
    line-height: 1.2;
    margin: 0;
  }
  .product-description {
    position: absolute;
    top: 802px;
    left: 0;
    width: 1034px;
    text-align: center;
    font-family: "Crimson Text", serif;
    font-style: italic;
    font-size: 24px;
    line-height: 33px;
    color: var(--ink);
    margin: 0;
  }
  .volume {
    position: absolute;
    top: 1068px;
    left: 0;
    width: 1034px;
    text-align: center;
    font-family: "Crimson Text", serif;
    font-size: 21px;
    color: #444;
    word-spacing: 6px;
  }
  .website {
    position: absolute;
    left: 1003px;
    top: 602px;
    transform: translate(-50%, -50%) rotate(-90deg);
    white-space: nowrap;
    font-family: "Lato", sans-serif;
    font-weight: 300;
    font-size: 24px;
    letter-spacing: 1px;
    color: var(--ink);
  }
</style>
</head>
<body>
<main class="label">
  <svg class="band band--top" viewBox="0 0 1034 110" aria-hidden="true">
    <defs>
      <linearGradient id="bandTopFill" x1="0" y1="0" x2="0" y2="1">
        <stop offset="0" stop-color="var(--plum-dark)"/>
        <stop offset="1" stop-color="var(--plum-light)"/>
      </linearGradient>
    </defs>
    <path d="M0 0 H1034 V72 H710 Q517 118 324 72 H0 Z" fill="url(#bandTopFill)"/>
  </svg>

  <div class="brand-mark" aria-hidden="true"></div>
  <div class="brand-name">Vellow Crest</div>
  <div class="tagline">Professional Styling Products</div>

  <h1 class="product-name">Shampoo</h1>
  <p class="product-description">100% natural hair &amp;<br>Scalp nourishment with<br>Acedic Acid &amp; Hemp<br>Omega 3 Oils.</p>

  <div class="volume">8 fl. oz. &nbsp;237 ml.</div>

  <div class="website">WWW.VELLOWCRESTINC.COM</div>

  <svg class="band band--bottom" viewBox="0 0 1034 110" aria-hidden="true">
    <defs>
      <linearGradient id="bandBottomFill" x1="0" y1="0" x2="0" y2="1">
        <stop offset="0" stop-color="var(--plum-light)"/>
        <stop offset="1" stop-color="var(--plum-dark)"/>
      </linearGradient>
    </defs>
    <path d="M0 110 H1034 V37 H710 Q517 -8 324 37 H0 Z" fill="url(#bandBottomFill)"/>
  </svg>
</main>
</body>
</html>
```